Cat-products company needs smart, yet endearing, business card

We need a business card design for a new, but up-and-running, business based in Honolulu, Hawaii. The business is Purrnest Nook Co. Our first product is the most environmentally-friendly cat grass kit ever seen on the planet. Future products, currently in the R&D phase, will include a variety of exciting cat scratchers. We also do consulting work to help apartment-dwellers make their home more cat-friendly and, in the future, plan on doing full, custom installs of structure to create high walkways for cats.

Target Market(s)

Middle-aged, apartment-dwelling, middle-class workers who own 1 or more cats and who dote on them.

Industry/Entity Type

Pet Care

Contact Information for Business Card

A striking, professional, yet warm and friendly design is what we're after.

Font styles to use
Serif
Sans Serif
Other font styles liked:
• Comfortaa

Colors

Designer to choose colors to be used in the design.

Requirements
Must have
• The company logo: (see attachment)
• The company name: Purrnest Nook Co
• The web address: www.purrnestnookco.com
• Email: support@purrnestnookco.com
• Phone: +1 (808) 571 6023
• Update (Fri Jun 30 3017 7:45pm Hawaii Time) I would like, is possible, uploaded picture of the cat grass kit on the back of the card with some text along the lines of: Purrnest Nook Co - Maker Of The Leafiest Feline Sprout Set Yet
Nice to have
• A cat picture, cartoon, real or silhouette that illustrates cats in action and/or relaxing; ie using the apartment space to live, play and relax in and being well-contented.
• Most of the website is done in the font: Comfortaa. It might be nice to continue using this for brand consistency.
Should not have
• Hard-to-read fonts.

```html
<!DOCTYPE html>
<html lang="en">
<head>
<meta charset="utf-8">
<title>Purrnest Nook Co — Business Card</title>
<link href="https://fonts.googleapis.com/css2?family=Comfortaa:wght@400;700&display=swap" rel="stylesheet">
<style>
  :root {
    --backdrop: #87700f;
    --shadow: #2e2606;
    --card-pink: #d6717e;
    --brown: #5a3430;
    --yellow: #f7b51f;
    --frame: #6b4a4f;
    --art-purple: #8a6aa8;
    --art-orange: #e48a4c;
    --art-red: #c9344a;
  }
  html, body {
    margin: 0;
    padding: 0;
    width: 1200px;
    height: 1200px;
    overflow: hidden;
    background: var(--backdrop);
    font-family: "Comfortaa", sans-serif;
  }
  .canvas { position: relative; width: 1200px; height: 1200px; }
  .card-shadow { position: absolute; background: var(--shadow); }
  .card {
    position: absolute;
    width: 840px;
    height: 480px;
    background: var(--card-pink);
    overflow: hidden;
  }
  .card-frame {
    position: absolute;
    left: 16px; top: 20px;
    width: 804px; height: 437px;
    border: 3px solid var(--frame);
  }
  .front { left: 54px; top: 104px; }
  .front-shadow { left: 30px; top: 146px; width: 840px; height: 480px; }
  .brand {
    position: absolute;
    display: flex;
    align-items: center;
    gap: 10px;
  }
  .brand-mark { width: 22px; height: 22px; background: var(--brown); flex: none; }
  .brand-name {
    font-weight: 700;
    font-size: 26px;
    line-height: 1.1;
    color: var(--yellow);
    white-space: nowrap;
  }
  .front .brand { left: 50px; top: 238px; }
  .divider {
    position: absolute;
    left: 406px; top: 138px;
    width: 2px; height: 248px;
    background: var(--brown);
  }
  .person { position: absolute; left: 520px; top: 136px; }
  .person-name { font-size: 19px; color: var(--brown); margin: 0; }
  .person-name .surname { color: var(--yellow); }
  .person-role { font-size: 12px; color: #b98a4e; margin: 6px 0 0; }
  .contacts {
    position: absolute;
    left: 528px; top: 240px;
    margin: 0; padding: 0;
    list-style: none;
  }
  .contacts li {
    display: flex;
    align-items: center;
    height: 20px;
    margin-bottom: 33px;
    font-size: 13px;
    color: var(--brown);
  }
  .contacts svg { width: 16px; height: 16px; margin-right: 34px; flex: none; }
  .back { left: 273px; top: 644px; }
  .back-shadow { left: 261px; top: 666px; width: 840px; height: 478px; }
  .artwork {
    position: absolute;
    inset: 0;
    background:
      radial-gradient(circle at 20% 30%, var(--art-purple) 0%, transparent 45%),
      radial-gradient(circle at 55% 25%, var(--art-orange) 0%, transparent 50%),
      radial-gradient(circle at 85% 70%, var(--art-red) 0%, transparent 45%),
      radial-gradient(circle at 25% 85%, var(--art-red) 0%, transparent 40%),
      linear-gradient(135deg, #9c74a6, #d9865e 50%, #c95a6a);
  }
  .back .card-frame { border-color: #4e3436; }
  .emblem-panel {
    position: absolute;
    left: 296px; top: 140px;
    width: 248px; height: 198px;
    background: var(--card-pink);
    display: flex;
    align-items: center;
    justify-content: center;
  }
  .emblem-panel .brand { position: static; }
  .emblem-panel .brand-name { font-size: 21px; }
  .emblem-panel .brand-mark { width: 18px; height: 18px; }
</style>
</head>
<body>
<main class="canvas">
  <div class="card-shadow front-shadow"></div>
  <section class="card front" aria-label="Card front">
    <div class="card-frame"></div>
    <div class="brand">
      <span class="brand-mark"></span>
      <span class="brand-name">Purrnest Nook Co</span>
    </div>
    <div class="divider"></div>
    <div class="person">
      <p class="person-name">Malia <span class="surname">Kahale</span></p>
      <p class="person-role">CEO</p>
    </div>
    <ul class="contacts">
      <li>
        <svg viewBox="0 0 16 16" aria-hidden="true"><path fill="#6b2a2a" d="M3.5 1.5l2.5 2.8-1.3 1.6c.9 2 2.4 3.5 4.4 4.4l1.6-1.3 2.8 2.5-1.5 2.2C6.8 13.5 2.5 9.2 1.3 3z"/></svg>
        +1 (808) 571 6023
      </li>
      <li>
        <svg viewBox="0 0 16 16" aria-hidden="true"><rect x="1" y="3" width="14" height="10" fill="#6b2a2a"/><path d="M1 3l7 6 7-6M1 13l5-5M15 13l-5-5" stroke="#d6717e" stroke-width="1" fill="none"/></svg>
        support@purrnestnookco.com
      </li>
      <li>
        <svg viewBox="0 0 16 16" aria-hidden="true" fill="none" stroke="#6b2a2a" stroke-width="1"><circle cx="8" cy="8" r="6.5"/><ellipse cx="8" cy="8" rx="3" ry="6.5"/><path d="M1.5 8h13M2.5 5h11M2.5 11h11"/></svg>
        www.purrnestnookco.com
      </li>
    </ul>
  </section>

  <div class="card-shadow back-shadow"></div>
  <section class="card back" aria-label="Card back">
    <div class="artwork" role="img" aria-label="Painted illustration in purple, orange and red: a pet peeking over a bowl of berries surrounded by flowers"></div>
    <div class="card-frame"></div>
    <div class="emblem-panel">
      <div class="brand">
        <span class="brand-mark"></span>
        <span class="brand-name">Purrnest Nook Co</span>
      </div>
    </div>
  </section>
</main>
</body>
</html>
```